Dwelvano - "Where Pest Control is Free for Life..." Please see pitch deck...

Project goal, that this is a reusable template, not a one-off card
Brand and design direction, follow the logo, use the brand palette (with a color swatch table), typography and layout guidance
The John Doe placeholder content as a clean field-by-field table (name, title, company, address, office, cell, fax, email, dwelvano.com)
Print specs, 3.5 × 2 in trim, 0.125 in bleed, 300 DPI, CMYK, crop marks
Deliverables, layered editable PSD (your primary ask) plus vector .AI/.EPS and a press-ready PDF/X-1a, with fonts packaged
What you'll provide (logo, colors, fonts)
Process and sign-off, concept first, then full file package on approval.
Populate every field with this John Doe placeholder data so we can see the layout fully built out. We will replace it per person.
Name John Doe
Title Title / Position
Company Dwelvano
Address 482 Oakline Avenue, Suite 210, Marlow Springs, FL 32415
Office (555) 014-2200
Cell (555) 014-2231
Fax (555) 014-2299
Email johndoe@dwelvano.com
Website dwelvano.com

We need the working, editable source files so we can update them ourselves, plus a ready-to-print export:
1. Photoshop (.PSD) — fully layered and editable, with each contact field on its own labeled text layer. This is the primary requested format.
2. Vector source — the press-standard editable format, Adobe Illustrator (.AI) and/or .EPS, since vector is preferred for crisp text and logos at print.
3. Print-ready PDF — press-quality (PDF/X-1a), CMYK, with bleed and crop marks, both sides.
4. Packaged fonts and links — include or list all fonts used, and package any linked assets so the files open correctly on our end.

Why both PSD and vector
The PSD covers our request directly and is easy for us to edit. Vector (.AI/.EPS) is what most commercial printers actually prefer for type and logos because it stays razor-sharp at any size. Providing both keeps us flexible no matter which printer we use. Have fun and keep it modern and cool the designer of the logo did a great job, see what you can do.

```html
<!DOCTYPE html>
<html lang="en">
<head>
<meta charset="UTF-8">
<title>Dwelvano Business Card Template</title>
<link href="https://fonts.googleapis.com/css2?family=Poppins:ital,wght@0,300;0,400;0,500;0,600;0,700;1,400&display=swap" rel="stylesheet">
<style>
  :root {
    --page-bg: #f1f1f1;
    --card-bg: #0a1124;
    --card-bg-soft: #10172b;
    --brand-teal: #03b5c6;
    --text-white: #ffffff;
    --text-body: #eef2f6;
  }
  * { margin: 0; padding: 0; box-sizing: border-box; }
  html, body {
    width: 1200px;
    height: 990px;
    overflow: hidden;
    background: var(--page-bg);
    font-family: "Poppins", sans-serif;
  }
  .canvas { position: relative; width: 1200px; height: 990px; }

  .card {
    position: absolute;
    left: 244px;
    width: 712px;
    height: 407px;
    background: var(--card-bg);
    border-left: 5px solid var(--brand-teal);
    border-bottom: 4px solid var(--brand-teal);
    box-shadow: 0 14px 30px rgba(0,0,0,0.28), 0 2px 8px rgba(0,0,0,0.18);
    overflow: hidden;
  }
  .card-front { top: 68px; }
  .card-back { top: 515px; }

  .emblem-area {
    position: absolute;
    background: linear-gradient(195deg, var(--brand-teal) 0%, #1b7f8c 22%, #0f2f40 45%, var(--card-bg-soft) 70%);
    border-radius: 0 14px 10px 0;
  }
  .card-front .emblem-area { left: 0; top: 0; width: 321px; height: 403px; }
  .card-back .emblem-area { right: 0; top: 152px; width: 202px; height: 251px; border-radius: 14px 0 0 0; }

  .wordmark {
    position: absolute;
    font-weight: 700;
    color: var(--text-white);
    letter-spacing: -0.5px;
    line-height: 1;
  }
  .card-front .wordmark { right: 30px; top: 330px; font-size: 44px; }
  .card-back .wordmark { left: 24px; top: 32px; font-size: 62px; letter-spacing: -1px; }

  .tagline {
    position: absolute;
    left: 25px;
    top: 99px;
    font-size: 15px;
    font-weight: 700;
    color: var(--text-white);
    letter-spacing: 1.6px;
  }
  .sub-tagline {
    position: absolute;
    left: 86px;
    top: 117px;
    font-size: 12px;
    font-style: italic;
    color: var(--brand-teal);
    letter-spacing: 0.4px;
  }

  .person {
    position: absolute;
    right: 27px;
    top: 28px;
    text-align: right;
  }
  .person-name { font-size: 36px; line-height: 1.1; color: var(--text-white); font-weight: 400; letter-spacing: 0.5px; }
  .person-name .first { color: var(--brand-teal); font-weight: 600; }
  .person-title { font-size: 18.5px; font-weight: 500; color: var(--text-white); letter-spacing: 0.6px; margin-top: 2px; }
  .name-bar {
    position: absolute;
    right: 0;
    top: 31px;
    width: 20px;
    height: 62px;
    background: var(--brand-teal);
  }

  .address {
    position: absolute;
    left: 20px;
    top: 188px;
    font-size: 18px;
    line-height: 24px;
    color: var(--text-body);
    letter-spacing: 0.4px;
  }
  .contact-list {
    position: absolute;
    left: 20px;
    top: 257px;
    list-style: none;
  }
  .contact-item {
    display: flex;
    align-items: center;
    height: 24px;
    font-size: 18.5px;
    color: var(--text-body);
    letter-spacing: 0.5px;
  }
  .contact-icon { width: 17px; height: 17px; margin-right: 10px; flex: none; }
</style>
</head>
<body>
<div class="canvas">

  <section class="card card-front" aria-label="Card front">
    <div class="emblem-area" role="img" aria-label="Large brand house emblem decoration"></div>
    <div class="wordmark">Dwelvano.com</div>
  </section>

  <section class="card card-back" aria-label="Card back">
    <div class="wordmark">Dwelvano</div>
    <div class="tagline">WE CARE WHERE YOU LIVE</div>
    <div class="sub-tagline">Friendly local service</div>

    <div class="person">
      <div class="person-name"><span class="first">John</span> Doe</div>
      <div class="person-title">Title / Position</div>
    </div>
    <div class="name-bar"></div>

    <div class="address">482 Oakline Avenue, Suite 210,<br>Marlow Springs, FL 32415</div>

    <ul class="contact-list">
      <li class="contact-item">
        <svg class="contact-icon" viewBox="0 0 24 24" fill="none" stroke="var(--brand-teal)" stroke-width="2" stroke-linecap="round" stroke-linejoin="round"><path d="M5 3h4l2 5-3 2a12 12 0 0 0 6 6l2-3 5 2v4a2 2 0 0 1-2 2A17 17 0 0 1 3 5a2 2 0 0 1 2-2z"/><path d="M15 3a6 6 0 0 1 6 6"/><path d="M15 7a2 2 0 0 1 2 2"/></svg>
        (555) 014-2200
      </li>
      <li class="contact-item">
        <svg class="contact-icon" viewBox="0 0 24 24" fill="none" stroke="var(--brand-teal)" stroke-width="2" stroke-linecap="round"><rect x="6" y="2" width="12" height="20" rx="2"/><path d="M11 18h2"/></svg>
        (555) 014-2231
      </li>
      <li class="contact-item">
        <svg class="contact-icon" viewBox="0 0 24 24" fill="var(--brand-teal)"><rect x="2" y="8" width="5" height="14" rx="1"/><rect x="8" y="10" width="14" height="12" rx="1"/><rect x="11" y="2" width="9" height="7" fill="none" stroke="var(--brand-teal)" stroke-width="1.6"/><g fill="var(--card-bg)"><rect x="10" y="13" width="2.5" height="2"/><rect x="14" y="13" width="2.5" height="2"/><rect x="18" y="13" width="2.5" height="2"/><rect x="10" y="17" width="2.5" height="2"/><rect x="14" y="17" width="2.5" height="2"/><rect x="18" y="17" width="2.5" height="2"/></g></svg>
        (555) 014-2299
      </li>
      <li class="contact-item">
        <svg class="contact-icon" viewBox="0 0 24 24" fill="none" stroke="var(--brand-teal)" stroke-width="2"><circle cx="12" cy="12" r="10"/><path d="M2 12h20M12 2c3 3 3 17 0 20M12 2c-3 3-3 17 0 20"/></svg>
        www.dwelvano.com
      </li>
      <li class="contact-item">
        <svg class="contact-icon" viewBox="0 0 24 24" fill="none" stroke="var(--brand-teal)" stroke-width="2" stroke-linejoin="round"><path d="M2 10l10-7 10 7v12H2z"/><path d="M2 10l10 7 10-7"/><circle cx="12" cy="10" r="2.5"/></svg>
        johndoe@dwelvano.com
      </li>
    </ul>

    <div class="emblem-area" role="img" aria-label="Brand house emblem decoration"></div>
  </section>

</div>
</body>
</html>
```